Brightline Energy Product Distribution Brochure

We are looking to have our current brochure for our customers completely redesigned...the idea is to present the relevant information in an attractive way . Our website is brightlineenergyco.example where you can find more information about us. We have included a file with a rough idea of the page order and what each should include but feel free to adapt based on design. The example provided is only for context and doesnt have to be maintained. We will be using the brochure both digitally and in print form. As long as it reads easily and is eye catching, the design can be horizontal or vertical.Final deliverable should be indesign file.

"Our Brands" page: should be limited to one page (space being enough) where it has the header for each one (for example diesel generators) space for one or two lines of text and then the corresponding logos for each of the five categories
Updates

For those asking: the "our brands" page should be a single page layout where there is a header with the corresponding section and space for maybe one line of text followed by the two logos for that category. Each of the product pages should be similar in fashion to the one in the document attached: a photo of the product with some white space and space for the text to be included. We will be posting additional examples today

Target Market(s)

We want to present it to customers both digitally and in print so they can see our products

Industry/Entity Type

Power Generation

Font styles to use
Serif

Requirements
Must have
• Eye catching and able to present the information in a presentable fashion. Rest is up to you.
Nice to have
• Should incorporate the colors of our logo but can also add other depending on design

```html
<!DOCTYPE html>
<html lang="en">
<head>
<meta charset="utf-8">
<title>Brightline Energy – Our Stock / Our Products</title>
<link href="https://fonts.googleapis.com/css2?family=Michroma&family=Poppins:wght@300;400;600;700&display=swap" rel="stylesheet">
<style>
  :root {
    --backdrop: #e4e4e2;
    --page: #ffffff;
    --page-shade: #dcdcdf;
    --ink: #2a2a2e;
    --ink-soft: #55555c;
    --brand-yellow: #f3d100;
    --brand-blue: #2f3193;
    --photo-light: #c9c1b4;
    --photo-mid: #8a7f70;
    --photo-dark: #3b352e;
  }
  * { box-sizing: border-box; margin: 0; padding: 0; }
  html, body { width: 1200px; height: 960px; overflow: hidden; background: var(--backdrop); }
  .spread {
    position: absolute; left: 30px; top: 250px;
    width: 1140px; height: 460px;
    background: var(--page);
    box-shadow: 0 14px 40px rgba(0,0,0,.18);
    overflow: hidden;
  }
  .spread__fold {
    position: absolute; left: 0; top: 0; width: 1140px; height: 460px;
    background: linear-gradient(90deg, transparent 0 44%, var(--page-shade) 50%, transparent 56%);
    opacity: .55;
  }
  .spread__art { position: absolute; inset: 0; }
  .stock { position: absolute; left: 60px; top: 48px; width: 310px; }
  .stock__title {
    font-family: "Michroma", sans-serif; font-weight: 400;
    color: var(--brand-yellow); font-size: 25px; letter-spacing: 1px;
  }
  .stock__intro {
    margin-top: 14px;
    font-family: "Poppins", sans-serif; font-weight: 300;
    font-size: 7.6px; line-height: 1.45; color: var(--ink-soft);
  }
  .stock__intro b { font-weight: 700; color: var(--ink); }
  .stock__list { list-style: none; margin-top: 12px; }
  .stock-bar {
    position: relative; height: 40px; margin-bottom: 7px;
    background: var(--brand-blue); color: #fff;
    font-family: "Poppins", sans-serif; font-weight: 300;
    font-size: 10px; line-height: 1.3;
    padding: 7px 96px 0 10px;
  }
  .stock-bar b { font-weight: 700; }
  .stock-bar__tag {
    position: absolute; right: 0; top: 0; width: 80px; height: 40px;
    background: var(--brand-yellow);
    clip-path: polygon(48% 0, 100% 0, 100% 100%, 0 100%);
  }
  .stock-bar__tag span {
    position: absolute; left: 30px; top: 13px;
    font-family: "Poppins", sans-serif; font-weight: 600; font-size: 10px;
    color: var(--brand-blue); transform: rotate(-40deg); white-space: nowrap;
  }
  .folio {
    position: absolute; left: 60px; bottom: 18px;
    font-family: "Poppins", sans-serif; font-size: 8px; color: var(--ink-soft);
  }
  .products-title {
    position: absolute; left: 700px; top: 396px;
    font-family: "Michroma", sans-serif; font-size: 27px; letter-spacing: 2px;
    color: #fff; text-shadow: 0 1px 3px rgba(0,0,0,.45);
  }
</style>
</head>
<body>
  <article class="spread">
    <svg class="spread__art" width="1140" height="460" viewBox="0 0 1140 460">
      <defs>
        <linearGradient id="engineTone" x1="0" y1="0" x2="1" y2="1">
          <stop offset="0" stop-color="var(--photo-light)"/>
          <stop offset=".45" stop-color="var(--photo-mid)"/>
          <stop offset="1" stop-color="var(--photo-dark)"/>
        </linearGradient>
      </defs>
      <path role="img" aria-label="Sepia close-up photograph of a diesel generator engine with turbocharger, alternator and radiator grille"
            d="M300 0 C420 60 520 260 640 460 L1140 460 L1140 330 C1070 240 1000 110 900 0 Z"
            fill="url(#engineTone)"/>
    </svg>
    <div class="spread__fold"></div>

    <section class="stock">
      <h2 class="stock__title">OUR STOCK</h2>
      <p class="stock__intro">
        <b>BRIGHTLINE ENERGY</b> offers you one of the largest inventories in North America of industrial generator sets to meet even the most urgent needs. Additionally, our company carries the single <b>largest stock of Automatic Voltage Regulators and Automatic Transfer Switches in the United States</b> with <b>1000+ units</b> of all major brands ready to ship SAME DAY to any country in the world.<br>
        We understand your urgency and we understand "same day". Our friendly staff will assist you same day, we will quote same day and we will ship <b>SAME DAY</b>.
      </p>
      <ul class="stock__list">
        <li class="stock-bar"><b>20+</b> generator trailers from<br><b>3500 to 10400 LBS</b> capacity.<div class="stock-bar__tag"><span>in stock</span></div></li>
        <li class="stock-bar"><b>50+</b> Fuel Tanks from<br><b>50 to 1000 Gal</b><div class="stock-bar__tag"><span>in stock</span></div></li>
        <li class="stock-bar"><b>100+</b> Automatic Transfer<br>Switches from <b>100 to 2000 AMPS</b><div class="stock-bar__tag"><span>in stock</span></div></li>
        <li class="stock-bar"><b>200+</b> Diesel Generators from<br><b>10 to 500 KW</b><div class="stock-bar__tag"><span>in stock</span></div></li>
        <li class="stock-bar" style="font-size:9px;padding-top:4px"><b>1000+</b> Engine parts, Alternator parts,<br>Generator parts, Automatic Voltage<br>Regulators and Generator controls<div class="stock-bar__tag"><span>in stock</span></div></li>
      </ul>
    </section>
    <span class="folio">6</span>

    <h2 class="products-title">OUR PRODUCTS</h2>
  </article>
</body>
</html>
```